Stock Broking Firm - Web Design Project

We are looking at doing a full re-design of our home page and content page and moving the majority of our content over to DNN.

Phase 1 : Website redesign www.kvtrading.com.au

The current design is too washed out, boring and has no call to action buttons.

Solution:

KV Trading is looking for a brighter/ cleaner redesign with a few stand out call to action buttons.

• Banner with logo across the top horizontally - Bright blue logo on white background similar to www.dlq.com.au - CALL 1300 482 917 - Follow on Chirpline / Friendwall
• Horizontal menu bar - professional looking. - Home - About Us- Our Services - Membership - Open an Account - Become a member - Contact
• Below banner top left - large rotating banner - maybe zumbo gallery style www.tgwhitfields.com.au
• Right of rotating banner - Membership login
• Below members login - Register for Daily Market Report/ research blog - Large bright button / Name / Email / Phone / pop up??
• Below Register for daily market report - Market Indicies - RSS feed of delayed data from QNX see www.tgwhitfields.com
• Below Market indicies - KV TRADING - Market Tweets ( feed from our chirpline page)

Below Rotating Banner -

content area

Below content area - 4 large block buttons see www.harkvine.com.au ( hover over change colour)

Button 1 - EDUCATION - content - click here for more

Button 2 - Market Information and Research

Button 3 - Full service Broker - content brief - click here for more

Button 4 - Trade Commodities and Options

below buttons - small horizontal menu bar slightly different colour incl - Careers/ Partners / Legal Privacy FSG Site Map

Regards,
Owen Pettit

Target Market(s)

35 - 65

Industry/Entity Type

Education

Requirements
Must have
• Follow brief above - large banner, call to action buttons, F.W. Chirpline, Member login etc. 4 big buttons
Nice to have
• clean looking site similar to www.dlq.com.au / not too busy. Corporate looking.
Should not have
• not too busy

```html
<!DOCTYPE html>
<html lang="en">
<head>
<meta charset="utf-8">
<title>KV Trading – Home</title>
<link rel="stylesheet" href="https://fonts.googleapis.com/css2?family=Ubuntu:wght@400;500&family=Open+Sans:wght@400;600&display=swap">
<style>
:root{
  --black:#000;
  --white:#fff;
  --brand-blue:#0e6a94;
  --sky:#35b6e8;
  --sky-pale:#dff3fb;
  --nav-dark:#1d1d1d;
  --nav-line:#4a4a4a;
  --orange:#f7a11a;
  --orange-dark:#f08a0c;
  --red:#c4161c;
  --grey-block:#959595;
  --grey-band:#d9d9d9;
  --grey-row:#efefef;
  --text:#222;
  --footer:#555;
}
*{box-sizing:border-box;margin:0;padding:0}
html,body{width:1125px;height:1200px;overflow:hidden;background:var(--black)}
body{font-family:"Open Sans",Arial,sans-serif;color:var(--text);font-size:12px}
.page{position:absolute;left:123px;top:0;width:878px;height:1200px;background:var(--white)}
.abs{position:absolute}

/* header */
.logo{left:9px;top:16px;width:304px;height:76px;background:#f4f6f8}
.logo-mark{left:10px;top:16px;width:30px;height:30px;background:var(--brand-blue)}
.logo-name{left:50px;top:2px;font-family:"Ubuntu",sans-serif;font-size:38px;line-height:48px;color:var(--brand-blue);white-space:nowrap}
.logo-tag{right:8px;top:50px;font-size:10px;color:#444;text-align:right;line-height:12px;white-space:nowrap}
.social-top{right:10px;top:10px;font-size:11.5px;display:flex;gap:12px}
.social-top span{display:flex;align-items:center;gap:5px}
.social-top i{display:inline-block;width:12px;height:12px;background:var(--brand-blue)}
.social-top span+span i{background:var(--sky)}
.phone-btn{left:626px;top:42px;width:243px;height:42px;border-radius:4px;background:linear-gradient(#e0262b,var(--red) 60%,#9e0f14);color:var(--white);font-family:"Ubuntu",sans-serif;font-size:25px;display:flex;align-items:center;padding-left:18px;gap:14px}

/* nav */
.nav{left:9px;top:107px;width:860px;height:38px;display:flex;border-bottom:3px solid var(--brand-blue)}
.nav a{color:var(--white);text-decoration:none;font-family:"Ubuntu",sans-serif;font-size:14px;display:flex;align-items:center;padding:0 10px;background:var(--nav-dark);border-right:1px solid var(--nav-line);height:34px;white-space:nowrap}
.nav .home{background:var(--brand-blue);width:36px;justify-content:center;padding:0}
.nav-secondary{flex:1;display:flex;align-items:center;justify-content:space-around;height:34px;background:var(--orange);color:#222;font-family:"Ubuntu",sans-serif;font-size:14px;padding:0 8px}
.nav-secondary a{background:none;color:#222;border:0;padding:0}

/* slider */
.slider{left:9px;top:161px;width:580px;height:380px;border:1px solid #ddd}
.slide-visual{left:7px;top:7px;width:563px;height:224px;background:linear-gradient(90deg,#dfe8ef,#bfd0dc 60%,#e8eef3)}
.slide-title{left:7px;top:236px;font-family:"Ubuntu",sans-serif;font-size:16px;color:var(--brand-blue)}
.slide-text{left:7px;top:262px;width:566px;font-size:11px;line-height:18px}
.slide-text em{color:var(--red)}
.thumbs{left:0;top:299px;width:578px;height:79px;background:var(--grey-band);display:flex;align-items:center;justify-content:center;gap:10px}
.thumb{width:94px;height:59px;border:2px solid #fff}
.thumb.active{border-color:var(--brand-blue)}
.arrow{color:#fff;font-size:22px}

/* blocks */
.block{width:282px;height:268px;background:var(--grey-block);color:var(--white)}
.block.edu{background:var(--brand-blue)}
.block h2{font-family:"Ubuntu",sans-serif;font-weight:400;font-size:21px;text-align:center;line-height:24px;height:68px;display:flex;align-items:center;justify-content:center}
.block .body{margin:0 9px;background:var(--white);color:var(--text);font-size:10.6px;line-height:17.5px;padding:8px 8px;height:174px}
.block .more{text-align:right;padding:6px 10px;font-size:11px}

/* sidebar */
.login{left:607px;top:161px;width:263px;height:313px;border:2px solid var(--brand-blue)}
.login-head{left:0;top:0;width:259px;height:76px;background:linear-gradient(#2a8dbb,var(--brand-blue));color:#fff;font-family:"Ubuntu",sans-serif;font-size:22px;text-align:center;padding-top:40px}
.login-badge{left:110px;top:-12px;width:40px;height:40px;border-radius:50%;background:var(--brand-blue);border:3px solid #fff}
.login label{position:absolute;left:15px;font-size:12px;color:#555}
.login .field{position:absolute;left:15px;width:228px;height:27px;background:#f1f1f1;border:1px solid #e3e3e3}
.login-links{left:15px;top:210px;font-size:12px;color:#555}
.login-links b{color:var(--red);font-weight:400}
.login-btn{left:15px;top:236px;width:228px;height:58px;background:linear-gradient(#3fb1df,#0c6f9b);color:#111;font-family:"Ubuntu",sans-serif;font-size:27px;display:flex;align-items:center;justify-content:center}
.cta{left:607px;width:263px;height:57px;color:#fff;font-family:"Ubuntu",sans-serif;font-size:17px;display:flex;align-items:center;justify-content:center}
.cta.orange{top:482px;background:linear-gradient(var(--orange),var(--orange-dark))}
.cta.dark{top:548px;background:linear-gradient(#5a5a5a,#111)}

.tab-head{left:607px;width:263px;height:33px;border-bottom:3px solid var(--sky)}
.tab-head span{display:inline-flex;align-items:center;height:30px;padding:0 14px;font-family:"Ubuntu",sans-serif;font-size:15px;color:#fff}
.indices-head{top:624px}
.indices-head span{background:var(--brand-blue)}
.rss{right:0;top:2px;width:24px;height:24px}
.indices{left:607px;top:662px;width:263px;border-collapse:collapse;font-size:11px}
.indices th{background:#9a9a9a;color:#fff;font-weight:400;height:33px;text-align:left;padding-left:16px}
.indices td{height:32.7px;padding-left:16px;color:#333;white-space:nowrap}
.indices tr:nth-child(odd) td{background:var(--grey-row)}
.indices tr:nth-child(even) td{background:var(--sky-pale)}
.tweets-head{top:907px}
.tweets-head span{background:var(--sky)}
.tweet-bird{right:2px;top:0;width:32px;height:26px;border-radius:50%;background:var(--sky)}
.tweet{left:607px;width:263px;display:flex;gap:9px;font-size:11px;line-height:18px;padding-bottom:6px}
.tweet .avatar{width:41px;height:41px;background:linear-gradient(#2e4f8a,#c33);border:2px solid #ccc;flex:none;margin-top:6px}
.tweet .handle{color:#888}
.tweet .tag{color:#2aa3d8}
.t1{top:947px;border-bottom:1px solid #e5e5e5}
.t2{top:1037px}

.footer{left:0;top:1164px;width:878px;height:36px;background:var(--footer);color:#fff;font-size:11px;display:flex;align-items:center;justify-content:space-between;padding:0 18px}
.footer .icons{display:flex;gap:6px}
.footer .icons i{width:23px;height:23px;border-radius:50%;background:#fff;display:block}
</style>
</head>
<body>
<div class="page">

  <header>
    <div class="abs logo">
      <div class="abs logo-mark"></div>
      <div class="abs logo-name">KV Trading</div>
      <div class="abs logo-tag">shares | options | commodities | foreign exchange<br>ABN 47 203 558 612 | licence no 528 604</div>
    </div>
    <div class="abs social-top"><span><i></i>Follow Us Friendwall</span><span><i></i>Follow Us Chirpline</span></div>
    <div class="abs phone-btn">
      <svg width="22" height="28" viewBox="0 0 22 28"><rect x="1" y="1" width="14" height="26" rx="2" fill="#fff"/><rect x="4" y="4" width="8" height="7" fill="#c4161c"/><path d="M17 9a5 5 0 0 1 0 8M19 6a9 9 0 0 1 0 14" stroke="#fff" stroke-width="1.6" fill="none"/></svg>
      1300 482 917
    </div>
  </header>

  <nav class="abs nav">
    <a class="home" href="#"><svg width="20" height="18" viewBox="0 0 20 18"><path d="M10 1 1 9h3v8h4v-5h4v5h4V9h3z" fill="#fff"/></svg></a>
    <a href="#">About Us</a><a href="#">Our Services</a><a href="#">Membership</a><a href="#">Open An Account</a><a href="#">Become a Member</a><a href="#">Contact</a>
    <div class="nav-secondary"><a href="#">Careers</a>|<a href="#">Partners</a>|<a href="#">Site Map</a></div>
  </nav>

  <section class="abs slider">
    <div class="abs slide-visual" role="img" aria-label="Banner photo: smiling businesswoman in front of pale blue stock chart graphics"></div>
    <div class="abs slide-title">Lorem Ipsum....</div>
    <p class="abs slide-text">Lorem Ipsum is simply dummy text of the printing and typesetting industry. Lorem Ipsum has been the industry's standard dummy text ever since the 1500s. <em>Read More....</em></p>
    <div class="abs thumbs">
      <span class="arrow">&#9664;</span>
      <div class="thumb active" role="img" aria-label="Thumbnail: businesswoman" style="background:linear-gradient(#dbe6ee,#a9bfcf)"></div>
      <div class="thumb" role="img" aria-label="Thumbnail: blue financial charts" style="background:linear-gradient(#2a6fb0,#9cc6e8)"></div>
      <div class="thumb" role="img" aria-label="Thumbnail: person before a world map screen" style="background:linear-gradient(#0b3fa8,#3a7ee0)"></div>
      <div class="thumb" role="img" aria-label="Thumbnail: man at desk with rising chart" style="background:linear-gradient(#f3f3f3,#d8d0c8)"></div>
      <div class="thumb" role="img" aria-label="Thumbnail: hand drawing a chart" style="background:linear-gradient(#e6edf3,#b7c8d6)"></div>
      <span class="arrow">&#9654;</span>
    </div>
  </section>

  <section>
    <div class="abs block edu" style="left:9px;top:557px">
      <h2>EDUCATION</h2>
      <p class="body">Contrary to popular belief, Lorem Ipsum is not simply random text. It has roots in a piece of classical Latin literature from 45 BC, making it over 2000 years old. Edwin Harlow, a Latin professor at Brookfield Hill College in Virginia, looked up one of the more obscure Latin words, consectetur, from a Lorem Ipsum passage, and going through the cites.</p>
      <div class="more">Click here for more &raquo;</div>
    </div>
    <div class="abs block" style="left:308px;top:557px">
      <h2>MARKET INFORMATION<br>&amp; RESEARCH</h2>
      <p class="body">Contrary to popular belief, Lorem Ipsum is not simply random text. It has roots in a piece of classical Latin literature from 45 BC, making it over 2000 years old. Edwin Harlow, a Latin professor at Brookfield Hill College in Virginia, looked up one of the more obscure Latin words, consectetur, from a Lorem Ipsum passage, and going through the cites.</p>
    </div>
    <div class="abs block" style="left:9px;top:842px">
      <h2>FULL SERVICE BROKER</h2>
      <p class="body">Contrary to popular belief, Lorem Ipsum is not simply random text. It has roots in a piece of classical Latin literature from 45 BC, making it over 2000 years old. Edwin Harlow, a Latin professor at Brookfield Hill College in Virginia, looked up one of the more obscure Latin words, consectetur, from a Lorem Ipsum passage, and going through the cites.</p>
      <div class="more">Click here for more &raquo;</div>
    </div>
    <div class="abs block" style="left:308px;top:842px">
      <h2>TRADE COMMODITIES<br>&amp; OPTIONS</h2>
      <p class="body">Contrary to popular belief, Lorem Ipsum is not simply random text. It has roots in a piece of classical Latin literature from 45 BC, making it over 2000 years old. Edwin Harlow, a Latin professor at Brookfield Hill College in Virginia, looked up one of the more obscure Latin words, consectetur, from a Lorem Ipsum passage, and going through the cites.</p>
    </div>
  </section>

  <aside>
    <div class="abs login">
      <div class="abs login-head">MEMBER LOGIN</div>
      <div class="abs login-badge"></div>
      <label style="top:86px">Username</label><div class="field" style="top:105px"></div>
      <label style="top:139px">Password</label><div class="field" style="top:158px"></div>
      <div class="abs login-links"><b>Register</b> &nbsp;|&nbsp; Forgot Password ?</div>
      <div class="abs login-btn">LOGIN</div>
    </div>
    <div class="abs cta orange">Register for Daily Market Report</div>
    <div class="abs cta dark">Register for Research Blog</div>

    <div class="abs tab-head indices-head"><span>Market Indices</span>
      <svg class="abs rss" viewBox="0 0 24 24"><rect width="24" height="24" rx="4" fill="#f7a11a"/><circle cx="6" cy="18" r="2.2" fill="#fff"/><path d="M4 11a9 9 0 0 1 9 9M4 5a15 15 0 0 1 15 15" stroke="#fff" stroke-width="2.6" fill="none"/></svg>
    </div>
    <table class="abs indices">
      <tr><th>NAME</th><th>VALUE</th><th>+/-</th><th>%+/-</th></tr>
      <tr><td>AU Broad</td><td>4,510.10</td><td>+4.60</td><td>+0.11</td></tr>
      <tr><td>AUS200</td><td>4,510.10</td><td>+4.60</td><td>+0.11</td></tr>
      <tr><td>US30</td><td>4,510.10</td><td>+4.60</td><td>+0.11</td></tr>
      <tr><td>US500</td><td>4,510.10</td><td>+4.60</td><td>+0.11</td></tr>
      <tr><td>HK50</td><td>4,510.10</td><td>+4.60</td><td>+0.11</td></tr>
      <tr><td>US100</td><td>4,510.10</td><td>+4.60</td><td>+0.11</td></tr>
    </table>

    <div class="abs tab-head tweets-head"><span>Market Tweets</span><div class="abs tweet-bird" role="img" aria-label="Bird illustration"></div></div>
    <div class="abs tweet t1"><div class="avatar" role="img" aria-label="Market report avatar"></div><p>KV Trading <span class="handle">@KVmarketdesk</span><br><span class="tag">#china</span> forecast lowered by <span class="tag">#ratedesk</span> &amp;<br><span class="tag">#velaro</span> back in POWER ... yeah!!!<br><span class="tag">Expand</span></p></div>
    <div class="abs tweet t2"><div class="avatar" role="img" aria-label="Market report avatar"></div><p>KV Trading <span class="handle">@KVmarketdesk</span><br><span class="tag">#china</span> forecast lowered by <span class="tag">#ratedesk</span> &amp;<br><span class="tag">#velaro</span> back in POWER ... yeah!!!<br><span class="tag">Expand</span></p></div>
  </aside>

  <footer class="abs footer">
    <span>Copyright © 2012 KV Trading. All Rights Reserved.</span>
    <div class="icons"><i></i><i></i><i></i></div>
  </footer>
</div>
</body>
</html>
```